New Business Card Design

We would like to refresh our business cards and make them look better. We are an IT company specialising in Cloud Services, IT Managed Services, software and hardware. I have attached a PSD of our current design. Also attached our logo.
Updates

I have uploaded all new logos in EPS format.

Can you please edit all designs to include a job title for Marcus Hollis, eg. General Manager

Industry/Entity Type

Software

Colors
ffffff

Requirements
Must have
• Please use white background.
Should not have
• Black background

```html
<!DOCTYPE html>
<html lang="en">
<head>
<meta charset="utf-8">
<title>Clarion Technology – Business Cards</title>
<link rel="stylesheet" href="https://fonts.googleapis.com/css2?family=Open+Sans:wght@400;600;700&display=swap">
<style>
  :root {
    --page-bg: #e9e9e7;
    --card-bg: #ffffff;
    --ink: #1f2428;
    --ink-soft: #333a40;
    --accent: #c8352a;
    --card-shadow: 0 6px 18px rgba(0, 0, 0, 0.18);
  }
  * { box-sizing: border-box; margin: 0; padding: 0; }
  html, body {
    width: 1200px;
    height: 720px;
    overflow: hidden;
    background: var(--page-bg);
    font-family: "Open Sans", Arial, sans-serif;
    color: var(--ink);
  }
  .stage {
    position: relative;
    width: 1200px;
    height: 720px;
  }
  .card {
    position: absolute;
    top: 210px;
    width: 525px;
    height: 300px;
    background: var(--card-bg);
    box-shadow: var(--card-shadow);
  }
  .card--front { left: 50px; }
  .card--back { left: 625px; }

  /* Brand lockup */
  .brand {
    position: absolute;
    display: flex;
    align-items: center;
    gap: 12px;
  }
  .brand__dot {
    flex: none;
    border-radius: 50%;
    background: var(--accent);
  }
  .brand__name {
    font-weight: 400;
    color: var(--ink);
    letter-spacing: 0.12em;
    text-transform: lowercase;
    white-space: nowrap;
  }
  .card--front .brand { left: 34px; top: 40px; }
  .card--front .brand__dot { width: 38px; height: 38px; }
  .card--front .brand__name { font-size: 28px; }

  .card--back .brand {
    left: 0; right: 0; top: 88px;
    justify-content: center;
  }
  .card--back .brand__name { font-size: 44px; letter-spacing: 0.14em; }

  /* Contact block */
  .person {
    position: absolute;
    left: 44px;
    top: 140px;
  }
  .person__name {
    font-size: 17px;
    font-weight: 700;
    color: var(--accent);
    line-height: 1.2;
  }
  .person__role {
    font-size: 12px;
    font-weight: 600;
    color: var(--ink-soft);
    margin-bottom: 12px;
  }
  .contact-list { list-style: none; }
  .contact-list__item {
    display: flex;
    align-items: center;
    gap: 9px;
    font-size: 12.5px;
    color: var(--ink-soft);
    line-height: 22px;
  }
  .contact-list__icon { width: 14px; height: 14px; flex: none; }

  /* Back tagline */
  .tagline {
    position: absolute;
    left: 0; right: 0; bottom: 44px;
    text-align: center;
    font-size: 16px;
    line-height: 1.45;
    color: var(--ink-soft);
  }
</style>
</head>
<body>
<main class="stage">

  <section class="card card--front" aria-label="Business card front">
    <div class="brand">
      <span class="brand__dot"></span>
      <span class="brand__name">clarion technology</span>
    </div>

    <div class="person">
      <p class="person__name">Marcus Hollis</p>
      <p class="person__role">General Manager</p>
      <ul class="contact-list">
        <li class="contact-list__item">
          <svg class="contact-list__icon" viewBox="0 0 14 14" aria-hidden="true">
            <circle cx="7" cy="7" r="7" fill="var(--accent)"/>
            <path d="M4.3 3.6 L5.6 3.4 L6.2 5.1 L5.4 5.8 Q6.1 7.4 7.9 8.5 L8.7 7.8 L10.4 8.4 L10.2 9.8 Q6 10.2 4.3 3.6 Z" fill="#fff"/>
          </svg>
          07 5550 1840
        </li>
        <li class="contact-list__item">
          <svg class="contact-list__icon" viewBox="0 0 14 14" aria-hidden="true">
            <circle cx="7" cy="7" r="7" fill="var(--accent)"/>
            <rect x="4.8" y="3" width="4.4" height="8" rx="0.8" fill="#fff"/>
            <rect x="5.5" y="4" width="3" height="4.8" fill="var(--accent)"/>
          </svg>
          0400 555 217
        </li>
        <li class="contact-list__item">
          <svg class="contact-list__icon" viewBox="0 0 14 14" aria-hidden="true">
            <circle cx="7" cy="7" r="7" fill="var(--accent)"/>
            <rect x="3.5" y="4.5" width="7" height="5" fill="#fff"/>
            <path d="M3.5 4.5 L7 7.3 L10.5 4.5" fill="none" stroke="var(--accent)" stroke-width="0.8"/>
          </svg>
          mhollis@clarionit.com.au
        </li>
        <li class="contact-list__item">
          <svg class="contact-list__icon" viewBox="0 0 14 14" aria-hidden="true">
            <circle cx="7" cy="7" r="7" fill="var(--accent)"/>
            <circle cx="7" cy="7" r="3.6" fill="none" stroke="#fff" stroke-width="0.9"/>
            <path d="M3.4 7 H10.6 M7 3.4 Q5 7 7 10.6 M7 3.4 Q9 7 7 10.6" fill="none" stroke="#fff" stroke-width="0.8"/>
          </svg>
          www.clarionit.com.au
        </li>
      </ul>
    </div>
  </section>

  <section class="card card--back" aria-label="Business card back">
    <div class="brand">
      <span class="brand__name">clarion technology</span>
    </div>
    <p class="tagline">
      We are an IT company specializing in Cloud Services<br>
      IT Managed Services, software and hardware
    </p>
  </section>

</main>
</body>
</html>
```